Vellisant - Quality health delivered at your door

Vellisant offers home and Community Based Services for adults who wish to continue live independently in their communities. We increase accessibility to health care, reduce health care delivery gap, reduce mortality and morbidity, reduce health while promoting healthy living in the comfort of our patients communities or homes.

We provide on site services and deliver high quality healthcare at your door. Our experienced physicians coordinate care with our certified nurse practitioners and provide chronic care management, physical therapy, rehabilitation and medications management.

Target Market(s)

Older population living in independent living facilities

Industry/Entity Type

Health Care

Contact Information for Business Card

Vellisant

Number of Pages Required

4 page

Font styles to use
Sans Serif

Colors

Designer to choose colors to be used in the design.

```html
<!DOCTYPE html>
<html lang="en">
<head>
<meta charset="utf-8">
<title>Vellisant – Quality health delivered at your door</title>
<link href="https://fonts.googleapis.com/css2?family=Open+Sans:wght@400;600;700&family=Oswald:wght@400;500&display=swap" rel="stylesheet">
<style>
:root{
  --orange:#f39a1e;
  --orange-dark:#e07f0c;
  --green:#3c5a1c;
  --green-dark:#2b4212;
  --beige:#f9eedd;
  --ink:#333;
  --muted:#8a8a8a;
  --white:#fff;
}
*{box-sizing:border-box;margin:0;padding:0}
html,body{width:889px;height:1200px;overflow:hidden}
body{font-family:"Open Sans",sans-serif;color:var(--ink);background:var(--white);position:relative}
.site-header{height:118px;position:relative;background:var(--white);border-bottom:5px solid var(--orange)}
.brand{position:absolute;left:22px;top:16px;display:flex;flex-direction:column;align-items:center}
.brand-mark{width:50px;height:50px;border-radius:50%;background:var(--orange)}
.brand-name{font-family:"Oswald",sans-serif;font-weight:500;font-size:24px;color:var(--green);margin-top:4px;letter-spacing:.5px}
.main-nav{position:absolute;right:26px;top:22px;display:flex;gap:0;font-size:11px;color:#555}
.main-nav a{color:inherit;text-decoration:none;padding:0 7px;border-left:1px solid #ccc}
.main-nav a:first-child{border-left:none}
.header-contact{position:absolute;right:26px;top:66px;display:flex;gap:14px}
.pill{background:var(--orange);color:var(--white);font-size:11px;font-weight:600;padding:5px 14px;border-radius:2px}
.hero{position:relative;height:487px;overflow:hidden}
.hero-photo{position:absolute;inset:0;background:linear-gradient(135deg,#c9b79a 0%,#8f7b62 40%,#5e5244 70%,#b59f82 100%)}
.hero-shade{position:absolute;inset:0;background:rgba(20,20,20,.35)}
.hero-copy{position:absolute;left:0;right:0;top:160px;text-align:center;color:var(--white)}
.hero-copy h1{font-family:"Oswald",sans-serif;font-weight:500;font-size:38px;letter-spacing:1px}
.hero-copy p{font-size:15px;line-height:1.45;width:430px;margin:14px auto 0}
.btn{display:inline-block;margin-top:20px;background:var(--white);color:var(--ink);font-size:14px;font-weight:600;padding:10px 22px;border-radius:3px}
.hero-wave{position:absolute;left:0;bottom:0;width:889px;height:90px}
.stay-home{background:var(--beige);height:175px;text-align:center;padding-top:18px}
.section-title{font-family:"Oswald",sans-serif;font-weight:500;font-size:28px;color:var(--green);letter-spacing:1px}
.stay-home p{font-size:11px;color:#666;line-height:1.55;width:700px;margin:8px auto 0}
.services{position:relative;padding-top:30px;text-align:center;height:420px}
.service-list{display:flex;justify-content:center;gap:30px;margin-top:24px}
.service{width:175px}
.service-icon{width:104px;height:104px;border-radius:50%;margin:0 auto;border:3px solid #ddd;display:flex;align-items:center;justify-content:center;background:var(--white)}
.service-icon.active{background:var(--orange);border-color:#f7c77e}
.service h3{font-size:13px;font-weight:700;color:var(--ink);margin-top:16px;line-height:1.3}
.service p{font-size:10.5px;color:var(--muted);margin-top:8px;line-height:1.45}
.arrow{position:absolute;top:190px}
.arrow.prev{left:36px}.arrow.next{right:36px}
.site-footer{position:absolute;left:0;right:0;bottom:0;height:132px}
.footer-bg{position:absolute;inset:0;width:889px;height:132px}
.footer-row{position:absolute;left:0;right:0;top:48px;display:flex;justify-content:center;gap:70px;color:var(--white);font-size:11px}
.footer-item{display:flex;align-items:center;gap:8px}
.footer-bottom{position:absolute;left:0;right:0;bottom:8px;display:flex;justify-content:space-between;padding:0 60px 0 300px;align-items:center}
.social{display:flex;gap:12px}
.social span{width:14px;height:14px;border-radius:50%;background:rgba(255,255,255,.85)}
.copyright{font-size:10px;color:var(--white)}
</style>
</head>
<body>
<header class="site-header">
  <div class="brand"><span class="brand-mark"></span><span class="brand-name">VELLISANT</span></div>
  <nav class="main-nav">
    <a>Assisted Living</a><a>Skilled Nursing</a><a>Independent Living</a><a>Services</a><a>Respite Care</a><a>Rehabilitation</a><a>FAQS</a>
  </nav>
  <div class="header-contact"><span class="pill">555-010-4420</span><span class="pill">CONTACT US</span></div>
</header>

<section class="hero">
  <div class="hero-photo" role="img" aria-label="Photo of smiling seniors sharing a meal together at a table"></div>
  <div class="hero-shade"></div>
  <div class="hero-copy">
    <h1>RETIREMENT YOU DESERVE</h1>
    <p>Lorem Ipsum is simply dummy text of the printing and typesetting industry. Lorem Ipsum has been the industry's standard dummy text.</p>
    <span class="btn">LEARN MORE</span>
  </div>
  <svg class="hero-wave" viewBox="0 0 889 90" preserveAspectRatio="none">
    <path d="M0 70 C250 85 500 20 889 10 L889 90 L0 90 Z" fill="var(--orange)"/>
    <path d="M0 80 C260 92 520 35 889 28 L889 90 L0 90 Z" fill="var(--beige)"/>
  </svg>
</section>

<section class="stay-home">
  <h2 class="section-title">STAY HOME</h2>
  <p>Vellisant offers Home and Community Based Services for adults who wish to continue to live independently in the comfort of their communities.</p>
  <p>We provide on site services and deliver high quality healthcare at your door. Our experienced physicians coordinate care with our certified nurse practitioners and provide chronic care management, physical therapy, rehabilitation and medications management.</p>
</section>

<section class="services">
  <h2 class="section-title">SERVICES</h2>
  <div class="service-list">
    <div class="service">
      <div class="service-icon active"><svg width="50" height="50" viewBox="0 0 50 50" fill="none" stroke="#fff" stroke-width="3"><path d="M12 8 v14 a10 10 0 0 0 20 0 v-14"/><path d="M22 32 v4 a8 8 0 0 0 16 0 v-6"/><circle cx="38" cy="26" r="4"/></svg></div>
      <h3>Comprehensive primary care services</h3>
      <p>Lorem Ipsum is simply dummy text of the printing and typesetting.</p>
    </div>
    <div class="service">
      <div class="service-icon"><svg width="50" height="50" viewBox="0 0 50 50" fill="none" stroke="#444" stroke-width="2.5"><circle cx="25" cy="14" r="7"/><path d="M10 44 c0-12 30-12 30 0"/></svg></div>
      <h3>Coordination of speciality care</h3>
      <p>Lorem Ipsum is simply dummy text of the printing and typesetting.</p>
    </div>
    <div class="service">
      <div class="service-icon"><svg width="50" height="50" viewBox="0 0 50 50" fill="none" stroke="#444" stroke-width="2.5"><path d="M25 42 L8 24 a9 9 0 0 1 17-10 a9 9 0 0 1 17 10 Z"/><path d="M12 26 h8 l3-6 4 10 3-4 h8"/></svg></div>
      <h3>Asthma, Diabetes mellitus, Heart</h3>
      <p>Lorem Ipsum is simply dummy text of the printing and typesetting.</p>
    </div>
    <div class="service">
      <div class="service-icon"><svg width="50" height="50" viewBox="0 0 50 50" fill="none" stroke="#444" stroke-width="2.5"><rect x="8" y="10" width="34" height="24" rx="2"/><path d="M18 42 h14 M25 34 v8"/><circle cx="25" cy="22" r="5"/></svg></div>
      <h3>Alzheimer's dementia</h3>
      <p>Lorem Ipsum is simply dummy text of the printing and typesetting.</p>
    </div>
  </div>
  <svg class="arrow prev" width="14" height="24" viewBox="0 0 14 24"><path d="M12 2 L3 12 L12 22" stroke="#444" stroke-width="3" fill="none"/></svg>
  <svg class="arrow next" width="14" height="24" viewBox="0 0 14 24"><path d="M2 2 L11 12 L2 22" stroke="var(--orange)" stroke-width="3" fill="none"/></svg>
</section>

<footer class="site-footer">
  <svg class="footer-bg" viewBox="0 0 889 132" preserveAspectRatio="none">
    <path d="M0 22 C300 0 600 0 889 14 L889 132 L0 132 Z" fill="var(--orange)"/>
    <path d="M0 28 C300 8 600 8 889 20 L889 132 L0 132 Z" fill="var(--green)"/>
    <rect x="0" y="100" width="889" height="32" fill="var(--green-dark)"/>
  </svg>
  <div class="footer-row">
    <div class="footer-item"><svg width="14" height="18" viewBox="0 0 14 18"><path d="M7 17 C2 10 1 8 1 6 a6 6 0 0 1 12 0 c0 2-1 4-6 11Z" fill="#fff"/><circle cx="7" cy="6" r="2" fill="var(--green)"/></svg><span>220 Linden Avenue<br>Fairview, ST 00000</span></div>
    <div class="footer-item"><svg width="16" height="16" viewBox="0 0 16 16"><path d="M3 1 l3 0 1 4 -2 1 c1 2 3 4 5 5 l1-2 4 1 0 3 c0 1-1 2-2 2 C7 15 1 9 1 3 c0-1 1-2 2-2Z" fill="#fff"/></svg><span>555-010-4420</span></div>
    <div class="footer-item"><svg width="18" height="14" viewBox="0 0 18 14"><rect x="1" y="1" width="16" height="12" fill="none" stroke="#fff" stroke-width="1.5"/><path d="M1 1 L9 8 L17 1" fill="none" stroke="#fff" stroke-width="1.5"/></svg><span>care@vellisant.example</span></div>
  </div>
  <div class="footer-bottom">
    <div class="social"><span></span><span></span><span></span></div>
    <div class="copyright">Copyright © 2017 VELLISANT. All Right Reserved</div>
  </div>
</footer>
</body>
</html>
```